wealth management firm, professional group, new model

we have a logo that works but we need a card, white background using our colors...clean look

our tag line if can be used in

Steady Guidance, Lasting Wealth

```html
<!DOCTYPE html>
<html lang="en">
<head>
<meta charset="utf-8">
<title>Varden Wealth Partners — Business Card</title>
<link rel="stylesheet" href="https://fonts.googleapis.com/css2?family=Montserrat:ital,wght@0,400;0,500;0,700;1,400&display=swap">
<style>
  :root {
    --navy: #1b2d57;
    --navy-deep: #14224a;
    --navy-light: #2c4175;
    --ink: #2a2d36;
    --muted: #5a5f6b;
    --paper: #ffffff;
    --stage: #e9eaee;
  }
  * { box-sizing: border-box; margin: 0; padding: 0; }
  html, body {
    width: 1200px; height: 900px; overflow: hidden;
    background: var(--stage);
    font-family: "Montserrat", Arial, sans-serif;
  }
  .canvas { position: relative; width: 1200px; height: 900px; }
  .card {
    position: absolute; left: 320px; width: 560px; height: 320px;
    border-radius: 22px; overflow: hidden;
    box-shadow: 0 10px 28px rgba(20, 30, 60, 0.18);
  }

  /* Front */
  .card-front { top: 70px; background: var(--paper); }
  .holder {
    position: absolute; left: 34px; top: 24px;
    padding-left: 14px; border-left: 8px solid var(--navy);
  }
  .holder-name { font-weight: 700; font-size: 24px; color: var(--navy); line-height: 1.1; }
  .holder-role { font-style: italic; font-size: 13px; color: var(--muted); margin-top: 3px; }
  .contact { position: absolute; left: 34px; top: 138px; list-style: none; }
  .contact li {
    display: flex; align-items: center; gap: 8px;
    font-size: 14px; color: var(--ink); line-height: 24px;
  }
  .contact svg { width: 12px; height: 12px; fill: var(--navy); flex: none; }
  .firm-name {
    position: absolute; right: 30px; top: 118px; width: 250px;
    text-align: left; font-weight: 500; font-size: 21px; line-height: 1.45;
    letter-spacing: 0.3em; color: var(--navy);
  }
  .tagline {
    position: absolute; right: 28px; bottom: 26px;
    font-size: 13px; color: var(--muted); letter-spacing: 0.02em; white-space: nowrap;
  }
  .base-band {
    position: absolute; right: 0; bottom: 0; width: 270px; height: 16px;
    background: var(--navy);
  }

  /* Back */
  .card-back { top: 510px; }
  .back-field {
    position: absolute; inset: 0;
    background: linear-gradient(135deg, var(--navy-light) 0%, var(--navy) 45%, var(--navy-deep) 100%);
  }
  .back-name {
    position: absolute; inset: 0; display: flex; align-items: center; justify-content: center;
    text-align: center; padding: 0 60px;
    font-weight: 500; font-size: 26px; line-height: 1.5; letter-spacing: 0.3em; color: var(--paper);
  }
</style>
</head>
<body>
<main class="canvas">

  <section class="card card-front" aria-label="Business card front">
    <div class="holder">
      <h1 class="holder-name">Corin Ashby</h1>
      <p class="holder-role">Managing Director</p>
    </div>

    <ul class="contact">
      <li>
        <svg viewBox="0 0 12 12" aria-hidden="true"><path d="M2.5 0.8 4.4 0.8 5.3 3.4 4 4.4C4.7 5.9 6 7.2 7.6 8L8.6 6.7 11.2 7.6 11.2 9.5C11.2 10.4 10.4 11.2 9.5 11.2 4.7 11.2 0.8 7.3 0.8 2.5 0.8 1.6 1.6 0.8 2.5 0.8Z"/></svg>
        555 018 204
      </li>
      <li>
        <svg viewBox="0 0 12 12" aria-hidden="true"><path d="M0.5 2.5H11.5V9.5H0.5Z M1.3 3.2 6 6.6 10.7 3.2" stroke="#fff" stroke-width="0.9"/></svg>
        hello@vardenwealth.com
      </li>
      <li>
        <svg viewBox="0 0 12 12" aria-hidden="true"><circle cx="6" cy="6" r="5.5"/><path d="M0.5 6H11.5M6 0.5C3.5 3.5 3.5 8.5 6 11.5M6 0.5C8.5 3.5 8.5 8.5 6 11.5" stroke="#fff" stroke-width="0.8" fill="none"/></svg>
        vardenwealth.com
      </li>
    </ul>

    <p class="firm-name">VARDEN WEALTH PARTNERS</p>

    <p class="tagline">Steady Guidance, Lasting Wealth</p>
    <div class="base-band"></div>
  </section>

  <section class="card card-back" aria-label="Business card back">
    <div class="back-field" role="img" aria-label="Deep navy field with a faint repeating arc pattern"></div>
    <p class="back-name">VARDEN WEALTH PARTNERS</p>
  </section>

</main>
</body>
</html>
```